Wesbite design for Investment Firm

We want a basic (clean) website that follows the form, fonts and colors of our attachments. This is for a financial investment management firm, but we have a boutique (anti-Wall Street) approach. Site should have an Home Page (Logo up top - room for basic copy on bottom, Philosophy Page (room for Quarterly Letter attachment and basic copy, Performance Page (room for Performance Overview and Performance Analysis and basic copy), Team Page, Commentary Page and Contact

Reason: Some designers have asked for an extension. Again, please only use image of Train Station or Train Station Logo in design.

Target Market(s)

Small and mid-size financial advisors from across the country

Industry/Entity Type

Financial

Number of Pages Required

5+ page

Font styles to use
Other font styles liked:
• Palotino Linotype

Colors
3176b5
cfdeed
ffffff

Requirements
Must have
• Please refer to existing site www.qlvor.example. Of note, this is too complex / cluttered. We simply want Blur, Grey and White consistent with attachments. The copy is pretty good, but will be simplified (and no quotes)
Should not have
• No images other than train station logo and / or train station image

```html
<!DOCTYPE html>
<html lang="en">
<head>
<meta charset="utf-8">
<title>Harlow Brook Investment Company</title>
<link rel="stylesheet" href="https://fonts.googleapis.com/css2?family=PT+Serif:ital,wght@0,400;0,700;1,400&display=swap">
<style>
:root{
  --blue:#3176b5;
  --blue-dark:#2a67a0;
  --pale:#cfdeed;
  --tab:#d7e4f1;
  --pale-bg:#f3f7fb;
  --team-bg:#e1eaf5;
  --footer-bg:#e8eef5;
  --white:#ffffff;
  --grey:#8a8f96;
  --ink:#3a3f45;
  --serif:"PT Serif", Georgia, serif;
}
*{box-sizing:border-box;margin:0;padding:0}
html,body{width:1200px;height:3214px;overflow:hidden}
body{position:relative;font-family:var(--serif);background:var(--white);color:var(--ink)}
.abs{position:absolute}
a{color:inherit;text-decoration:none}

/* header */
.site-header{position:absolute;left:0;top:0;width:1200px;height:146px;background:var(--blue)}
.brand-tab{position:absolute;left:0;top:0;width:1200px;height:92px}
.brand-name{position:absolute;left:0;top:20px;width:1200px;text-align:center;font-size:37px;line-height:46px;white-space:nowrap;color:var(--blue)}
.social-top{position:absolute;left:79px;top:10px;display:flex;gap:12px}
.social-top span{width:26px;height:26px;border-radius:50%;background:var(--white);display:block}
.utility{position:absolute;right:79px;top:13px;font-size:15px;color:var(--white)}
.utility .sep{margin:0 8px;opacity:.7}
.main-nav{position:absolute;left:0;top:100px;width:1200px;display:flex;justify-content:center;gap:34px;font-size:21px;color:var(--white)}
.main-nav .active{border-bottom:2px solid var(--white);padding-bottom:4px}

/* hero */
.hero{position:absolute;left:0;top:146px;width:1200px;height:574px;background:linear-gradient(100deg,#dfe6ec 0%,#c9d6e0 40%,#a9b9c4 65%,#8a8e86 100%)}
.hero h1{position:absolute;left:79px;top:160px;font-size:50px;line-height:60px;color:var(--blue);font-weight:700;white-space:nowrap}
.hero p{position:absolute;left:79px;top:226px;width:620px;font-size:14px;line-height:22px;font-weight:700;color:#2b2f35}
.btn{position:absolute;display:flex;align-items:center;justify-content:center;font-size:20px;font-weight:700;letter-spacing:.5px;border-radius:10px;white-space:nowrap}
.btn-light{background:var(--white);color:var(--blue)}
.btn-blue{background:var(--blue);color:var(--white)}
.slider-dots{position:absolute;left:576px;top:542px;display:flex;gap:6px}
.slider-dots span{width:18px;height:12px;background:var(--blue);opacity:.6}
.slider-dots span.on{opacity:1}

/* sections */
.section-title{position:absolute;color:var(--blue);font-weight:700;white-space:nowrap}
.body-copy{position:absolute;font-size:15px;line-height:24px;color:var(--grey)}
.doc-thumb{position:absolute;background:#c6c8cb;padding:12px}
.doc-thumb div{width:100%;height:100%;background:linear-gradient(#fbfbfb,#f0f0f0);border:1px solid #9a9a9a}

.philosophy{position:absolute;left:0;top:1108px;width:1200px;height:572px;background:var(--pale-bg)}
.quote-line{position:absolute;left:300px;width:600px;text-align:center;font-size:15px;line-height:26px;color:var(--grey)}
.quote-line b{color:var(--ink)}
.pillar{position:absolute;width:300px;text-align:center}
.pillar-ring{display:block;margin:0 auto;width:150px;height:150px}
.pillar h3{margin-top:44px;font-size:21px;color:var(--blue);white-space:nowrap}
.pillar p{margin:10px auto 0;width:250px;font-size:15px;line-height:25px;color:var(--grey)}

.performance-quote{position:absolute;left:343px;top:1780px;font-size:16px;font-weight:700;color:var(--ink);white-space:nowrap}

.team{position:absolute;left:0;top:2057px;width:1200px;height:468px;background:var(--team-bg)}
.member{position:absolute;width:262px;height:103px;background:var(--white);top:219px}
.member .avatar{position:absolute;left:63px;top:-81px;width:136px;height:136px;border-radius:50%;border:5px solid var(--white);background:radial-gradient(circle at 50% 40%,#e8d9cb 0%,#b8a89a 55%,#7c8a99 100%)}
.member h4{position:absolute;left:0;top:64px;width:262px;text-align:center;font-size:21px;color:var(--blue);white-space:nowrap}

.testimonial p{position:absolute;left:255px;top:2662px;width:690px;font-size:15px;line-height:26px;color:var(--grey);text-align:center}
.testimonial .author{position:absolute;left:0;top:2746px;width:1200px;text-align:center;font-size:16px;font-weight:700;color:var(--blue)}

/* footer */
.site-footer{position:absolute;left:0;top:2829px;width:1200px;height:278px;background:var(--footer-bg)}
.footer-nav{position:absolute;left:79px;top:70px;display:flex;gap:26px;font-size:19px;color:var(--ink);white-space:nowrap}
.footer-nav .active{color:var(--blue)}
.social-foot{position:absolute;left:892px;top:61px;display:flex;gap:18px}
.social-foot span{width:46px;height:46px;border-radius:50%;background:var(--white);display:block}
.social-foot span.on{background:var(--blue)}
.footer-rule{position:absolute;left:79px;top:136px;width:1042px;height:1px;background:#c9d3de}
.contact-col{position:absolute;top:170px}
.contact-col svg{position:absolute;left:0;top:4px}
.contact-col h5{margin-left:54px;font-size:21px;font-weight:400;color:var(--blue);white-space:nowrap}
.contact-col p{margin-left:54px;margin-top:6px;font-size:14px;line-height:24px;color:var(--ink);white-space:nowrap}

.bottom-bar{position:absolute;left:0;top:3107px;width:1200px;height:107px;background:var(--blue)}
.subscribe{position:absolute;left:79px;top:26px;width:612px;height:56px;background:var(--white);border-radius:28px;border:3px solid var(--pale)}
.subscribe .label{position:absolute;left:60px;top:14px;font-size:16px;color:var(--ink)}
.subscribe .go{position:absolute;right:6px;top:6px;width:176px;height:38px;border-radius:19px;background:var(--pale);color:var(--blue);font-size:17px;display:flex;align-items:center;justify-content:center}
.copyright{position:absolute;left:836px;top:34px;font-size:14px;line-height:20px;color:var(--white);letter-spacing:.5px;white-space:nowrap}
</style>
</head>
<body>

<header class="site-header">
  <svg class="brand-tab" width="1200" height="92" viewBox="0 0 1200 92"><polygon points="256,0 944,0 918,92 282,92" fill="#d7e4f1"/></svg>
  <div class="brand-name">Harlow Brook Investment Company</div>
  <div class="social-top" aria-label="Social links"><span></span><span></span><span></span></div>
  <div class="utility">English<span class="sep">|</span>Log in &#8594;</div>
  <nav class="main-nav">
    <a class="active">Home</a><a>Philosophy</a><a>Performance</a><a>Team</a><a>Letters</a><a>Commentary</a><a>Contact</a>
  </nav>
</header>

<section class="hero" role="img" aria-label="Photo of a couple looking out over a city skyline">
  <h1>What is your next plan...?</h1>
  <p>We founded Harlow Brook Investment Company in 1999, initially managing wealth from our family and friends in the town of Harlow Brook. The high expectations of our original investors is a key contributor to our value driven investment philosophy.</p>
  <a class="btn btn-light" style="left:79px;top:325px;width:206px;height:50px">LEARN MORE</a>
  <div class="slider-dots"><span></span><span class="on"></span></div>
</section>

<section class="about">
  <h2 class="section-title" style="left:79px;top:770px;font-size:37px">About Harlow Brook Investment Company</h2>
  <p class="body-copy" style="left:79px;top:834px;width:750px">We founded Harlow Brook Investment Company in 1999, initially managing wealth from our family and friends in the town of Harlow Brook. The high expectations of our original investors is a key contributor to our value driven investment philosophy.Based in Fairview, TX, we manage assets for both individuals and institutions. Our investment methodology stresses absolute returns vs. relative performance, blending a combination of fundamental analysis, discipline and patience with the goal of preserving and compounding capital.</p>
  <a class="btn btn-blue" style="left:79px;top:988px;width:168px;height:56px">LEARN MORE</a>
  <div class="doc-thumb" style="left:879px;top:761px;width:164px;height:282px"><div role="img" aria-label="Cover of the quarterly investment letter"></div></div>
</section>

<section class="philosophy">
  <h2 class="section-title" style="left:0;top:45px;width:1200px;text-align:center;font-size:37px">Philosophy</h2>
  <p class="quote-line" style="top:105px">"The stock market is filled with individuals who know the price of everything,but the value of nothing." <b>- Martin Easel</b></p>

  <div class="pillar" style="left:118px;top:199px">
    <svg class="pillar-ring" viewBox="0 0 150 150"><circle cx="75" cy="75" r="72" fill="#fff" stroke="#a9c4e0" stroke-width="5"/><circle cx="75" cy="75" r="60" fill="#dbe6f2"/>
      <g fill="#3176b5"><path d="M58 92 L84 56 L102 60 L104 78 L78 106 Z" transform="rotate(8 75 75)"/></g>
      <circle cx="95" cy="66" r="4" fill="#dbe6f2"/>
      <text x="74" y="88" font-size="22" font-family="PT Serif, serif" fill="#fff" text-anchor="middle" transform="rotate(-40 74 82)">$</text></svg>
    <h3>Buy at a Discount</h3>
    <p>Our proprietary investment research seeks to determine the appraised value of a company.</p>
  </div>

  <div class="pillar" style="left:450px;top:199px">
    <svg class="pillar-ring" viewBox="0 0 150 150"><circle cx="75" cy="75" r="72" fill="#fff" stroke="#a9c4e0" stroke-width="5"/><circle cx="75" cy="75" r="60" fill="#dbe6f2"/>
      <g fill="#3176b5"><circle cx="68" cy="60" r="13"/><path d="M44 100 Q46 78 68 76 Q80 76 86 82 L74 100 Z"/><path d="M88 76 L106 104 L70 104 Z"/></g>
      <rect x="86.5" y="86" width="3" height="9" fill="#fff"/><rect x="86.5" y="97" width="3" height="3" fill="#fff"/></svg>
    <h3>Emphasis on Risk</h3>
    <p>Our proprietary investment research seeks to determine the appraised value of a company.</p>
  </div>

  <div class="pillar" style="left:782px;top:199px">
    <svg class="pillar-ring" viewBox="0 0 150 150"><circle cx="75" cy="75" r="72" fill="#fff" stroke="#a9c4e0" stroke-width="5"/><circle cx="75" cy="75" r="60" fill="#dbe6f2"/>
      <circle cx="78" cy="60" r="15" fill="none" stroke="#3176b5" stroke-width="4"/>
      <text x="78" y="67" font-size="20" font-family="PT Serif, serif" fill="#3176b5" text-anchor="middle" font-weight="700">$</text>
      <g fill="#3176b5"><rect x="44" y="84" width="10" height="22"/><path d="M56 86 L76 84 Q84 84 86 90 L98 86 Q106 84 106 92 L82 104 L56 104 Z"/></g></svg>
    <h3>Willingness to Hold Cash</h3>
    <p>Our proprietary investment research seeks to determine the appraised value of a company.</p>
  </div>
</section>

<section class="performance">
  <div class="doc-thumb" style="left:79px;top:1732px;width:210px;height:265px"><div role="img" aria-label="Performance overview report with charts and tables"></div></div>
  <h2 class="section-title" style="left:343px;top:1730px;font-size:37px">Performance</h2>
  <p class="performance-quote">"Mimicking the herd invites regression to the mean."- Walter Brisk</p>
  <p class="body-copy" style="left:343px;top:1818px;width:780px">We believe trying to keep pace with the market in all environments promotes poor decisions and increases the probability of making mistakes. By focusing on the process and decisions, outcomes take care of themselves. Ultimately, an absolute return mindset outperforms by protecting capital in down markets while producing positive returns in up markets</p>
  <a class="btn btn-blue" style="left:343px;top:1941px;width:167px;height:56px">LEARN MORE</a>
</section>

<section class="team">
  <h2 class="section-title" style="left:0;top:50px;width:1200px;text-align:center;font-size:37px">Philosophy</h2>
  <div class="member" style="left:129px"><div class="avatar" role="img" aria-label="Portrait of team member"></div><h4>Dale P. Orwin</h4></div>
  <div class="member" style="left:469px"><div class="avatar" role="img" aria-label="Portrait of team member"></div><h4>Henry T. Mallory</h4></div>
  <div class="member" style="left:810px"><div class="avatar" role="img" aria-label="Portrait of team member"></div><h4>Nina Calder</h4></div>
  <a class="btn btn-blue" style="left:516px;top:369px;width:168px;height:51px;border-radius:0;font-size:18px">VIEW ALL &#187;</a>
</section>

<section class="testimonial">
  <h2 class="section-title" style="left:0;top:2574px;width:1200px;text-align:center;font-size:37px">What Our Client Say</h2>
  <svg class="abs" style="left:198px;top:2638px" width="40" height="30" viewBox="0 0 40 30"><g fill="#3176b5"><path d="M0 30 V16 Q0 2 16 0 V6 Q8 8 8 14 H16 V30 Z"/><path d="M22 30 V16 Q22 2 38 0 V6 Q30 8 30 14 H38 V30 Z"/></g></svg>
  <p>Lorem Ipsum is simply dummy text of the printing and typesetting industry. Lorem Ipsum has been the industry's standard dummy text ever since the 1500s, when an unknown printer took a galley of type and scrambled it to make a type specimen book.</p>
  <div class="author">- Paul R. Ashby</div>
</section>

<footer class="site-footer">
  <nav class="footer-nav"><a class="active">Home</a><a>Philosophy</a><a>Performance</a><a>Team</a><a>Letters</a><a>Commentary</a><a>Contact</a></nav>
  <div class="social-foot" aria-label="Social links"><span class="on"></span><span></span><span></span><span></span></div>
  <div class="footer-rule"></div>

  <div class="contact-col" style="left:79px">
    <svg width="26" height="38" viewBox="0 0 26 38"><path d="M13 0 C5 0 0 6 0 13 C0 22 13 38 13 38 C13 38 26 22 26 13 C26 6 21 0 13 0 Z" fill="#3176b5"/><circle cx="13" cy="13" r="5" fill="#e8eef5"/></svg>
    <h5>Our Location</h5>
    <p>1200 Elm Row Avenue,<br>Suite 310 Fairview, TX 75010</p>
  </div>
  <div class="contact-col" style="left:467px">
    <svg width="40" height="38" viewBox="0 0 40 38"><g fill="#3176b5"><rect x="0" y="10" width="10" height="28" rx="3"/><rect x="13" y="0" width="27" height="38" rx="2"/></g><g fill="#e8eef5"><rect x="17" y="5" width="19" height="7"/><rect x="17" y="16" width="5" height="4"/><rect x="24" y="16" width="5" height="4"/><rect x="31" y="16" width="5" height="4"/><rect x="17" y="23" width="5" height="4"/><rect x="24" y="23" width="5" height="4"/><rect x="31" y="23" width="5" height="4"/><rect x="17" y="30" width="5" height="4"/><rect x="24" y="30" width="5" height="4"/><rect x="31" y="30" width="5" height="4"/></g></svg>
    <h5>Call Us</h5>
    <p>555.010.4821<br>Customer Support Toll free</p>
  </div>
  <div class="contact-col" style="left:829px">
    <svg width="42" height="38" viewBox="0 0 42 38"><path d="M2 16 L21 2 L40 16 V38 H2 Z" fill="#3176b5"/><rect x="9" y="8" width="24" height="18" fill="#e8eef5"/><rect x="13" y="12" width="16" height="2" fill="#3176b5"/><rect x="13" y="17" width="16" height="2" fill="#3176b5"/><path d="M2 16 L21 30 L40 16" fill="none" stroke="#e8eef5" stroke-width="2"/></svg>
    <h5>Email Us</h5>
    <p>info@qlvor.example</p>
  </div>
</footer>

<div class="bottom-bar">
  <div class="subscribe">
    <svg class="abs" style="left:20px;top:16px" width="28" height="20" viewBox="0 0 28 20"><rect x="1" y="1" width="26" height="18" rx="2" fill="none" stroke="#3176b5" stroke-width="2"/><path d="M1 2 L14 12 L27 2" fill="none" stroke="#3176b5" stroke-width="2"/></svg>
    <span class="label">Email :</span>
    <span class="go">SUBSCRIBE!</span>
  </div>
  <p class="copyright">© HARLOW BROOK INVESTMENT COMPANY<br>2017 &nbsp;All Rights Reserved</p>
</div>

</body>
</html>
```